Maris Dovey Studio Business Cards

Hi - using the information and logo provided I require a two sided business card designed with the following information. The business card is a 'mini card' 3.5" x 1.25".

Front of card should be the logo attached but inverted (so the background is the peach colour and the logo white).

Back should have these details. If we can't fit the Pictogrum and Friendwall part can we just put the little logos.

Tessa Varnold

Art and Design Consultant
Dealer - Curator - Events - Styling - Creative Sourcing

P: 0438 217 604
E: tessa@marisdoveystudio.example
W: www.marisdoveystudio.example
I (pictogram image please): marisdoveystudio F (Friendwall image please): MarisDoveyAdviser

Target Market(s)

Galleries, artists, art buyers, interior design clients, event managers, creative types

Industry/Entity Type

Business

```html
<!DOCTYPE html>
<html lang="en">
<head>
<meta charset="utf-8">
<title>Maris Dovey Studio – Business Cards</title>
<link rel="stylesheet" href="https://fonts.googleapis.com/css2?family=Cabin:wght@400&family=Tinos&display=swap">
<style>
  :root {
    --stage: #6b5a50;
    --teal: #3bb08a;
    --teal-light: #5cc4a3;
    --peach: #f2b79a;
    --slate: #6c6d70;
    --wordmark-grey: #6d6a6a;
    --white: #ffffff;
    --rule-light: rgba(255, 255, 255, 0.35);
  }
  * { margin: 0; padding: 0; box-sizing: border-box; }
  html, body { width: 1200px; height: 960px; overflow: hidden; }
  body { background: var(--stage); position: relative; font-family: "Cabin", sans-serif; }

  .card { position: absolute; width: 866px; height: 308px; overflow: hidden; }

  /* Front */
  .card-front {
    left: 50px; top: 50px;
    background: radial-gradient(ellipse at 50% 45%, var(--teal-light) 0%, var(--teal) 55%);
  }
  .brand-mark {
    position: absolute; left: 363px; top: 14px;
    width: 140px; height: 140px; border-radius: 50%;
    background: var(--peach);
  }
  .brand-name {
    position: absolute; left: 0; right: 0; top: 176px;
    text-align: center; font-family: "Tinos", serif;
    font-size: 30px; letter-spacing: 6px; color: var(--wordmark-grey);
  }
  .service-band {
    position: absolute; left: 0; right: 0; top: 253px; height: 39px;
    border-top: 1px solid var(--rule-light); border-bottom: 1px solid var(--rule-light);
    display: flex; align-items: center; justify-content: center;
    font-family: "Tinos", serif; font-size: 22px; letter-spacing: 3px; color: var(--white);
  }

  /* Back */
  .card-back { left: 296px; top: 464px; background: var(--slate); }
  .profile-icon {
    position: absolute; left: 37px; top: 37px; width: 48px; height: 58px;
    border-radius: 8px; background: var(--teal);
  }
  .person-name {
    position: absolute; left: 100px; top: 26px;
    font-size: 41px; color: var(--peach); line-height: 1;
  }
  .person-role {
    position: absolute; left: 100px; top: 80px;
    font-size: 19px; color: var(--white);
  }
  .name-rule {
    position: absolute; left: 32px; top: 116px; width: 440px; height: 2px;
    background: var(--peach);
  }
  .contact-list { position: absolute; left: 33px; top: 133px; }
  .contact-row { display: flex; height: 30px; align-items: center; font-size: 19px; }
  .contact-label { width: 80px; color: var(--peach); }
  .contact-colon { width: 20px; color: var(--white); }
  .contact-value { color: var(--white); }
  .social-list { position: absolute; left: 496px; top: 136px; }
  .social-row { display: flex; align-items: center; height: 52px; color: var(--white); }
  .social-square { width: 14px; height: 14px; background: var(--white); margin-right: 8px; }
  .social-network { width: 86px; font-size: 15px; }
  .social-handle { font-size: 19px; }
  .studio-band {
    position: absolute; left: 0; right: 0; top: 250px; height: 30px;
    border-top: 1px solid var(--rule-light); border-bottom: 1px solid var(--rule-light);
    display: flex; align-items: center; justify-content: center;
    font-size: 19px; letter-spacing: 5px; color: var(--peach);
  }
</style>
</head>
<body>
  <section class="card card-front">
    <div class="brand-mark"></div>
    <div class="brand-name">MARIS DOVEY STUDIO</div>
    <div class="service-band">Dealer | Curator | Events | Styling | Creative Sourcing</div>
  </section>

  <section class="card card-back">
    <div class="profile-icon" role="img" aria-label="Profile icon"></div>
    <div class="person-name">Tessa Varnold</div>
    <div class="person-role">Art and Design Consultant</div>
    <div class="name-rule"></div>

    <div class="contact-list">
      <div class="contact-row"><span class="contact-label">Phone</span><span class="contact-colon">:</span><span class="contact-value">0438 217 604</span></div>
      <div class="contact-row"><span class="contact-label">Email</span><span class="contact-colon">:</span><span class="contact-value">tessa@marisdoveystudio.example</span></div>
      <div class="contact-row"><span class="contact-label">Web</span><span class="contact-colon">:</span><span class="contact-value">www.marisdoveystudio.example</span></div>
    </div>

    <div class="social-list">
      <div class="social-row"><span class="social-square"></span><span class="social-network">Pictogrum</span><span class="social-handle">MarisDoveyAdviser</span></div>
      <div class="social-row"><span class="social-square"></span><span class="social-network">Friendwall</span><span class="social-handle">marisdoveystudio</span></div>
    </div>

    <div class="studio-band">MARIS DOVEY STUDIO</div>
  </section>
</body>
</html>
```